Meridale Bed Company Needs Business Card

Looking for a very nice looking business card. Creative but not extravagant. We sell beds and pillows across the U.S. and need something professional but catchy. I have attached the logo.

Name : Devin Holt
Title : President
Phone : (800) 471-2960
Email: sleep@quilmora.com
Website: www.quilmora.com

Can be single-sided or double-sided
horizontal or vertical

Can use Blues/Greys

Target Market(s)

Mass Market

Industry/Entity Type

Retail

Contact Information for Business Card

Name : Devin Holt
Title : President
Phone : (800) 471-2960
Email: sleep@quilmora.com
Website: www.quilmora.com

Requirements
Must have
• Clean, Modern, Smooth
• Can use Blues/Greys
• On the other side without the information - have something simple like www.quilmora.com or our logo
Nice to have
• Surprise me
Should not have
• Nothing crazy, nothing cluttered

```html
<!DOCTYPE html>
<html lang="en">
<head>
<meta charset="utf-8">
<title>Meridale Bed Company – Business Card</title>
<link rel="stylesheet" href="https://fonts.googleapis.com/css2?family=Source+Sans+3:wght@300;400;700&display=swap">
<style>
  :root {
    --backdrop: #d6d6d6;
    --card: #ffffff;
    --blue: #36a4d6;
  }
  * { margin: 0; padding: 0; box-sizing: border-box; }
  html, body {
    width: 1200px;
    height: 1200px;
    overflow: hidden;
    background: var(--backdrop);
    font-family: "Source Sans 3", "Myriad Pro", Arial, sans-serif;
  }
  .canvas { position: relative; width: 1200px; height: 1200px; }
  .card {
    position: absolute;
    top: 206px;
    width: 417px;
    height: 730px;
    background: var(--card);
    overflow: hidden;
  }
  .card--front { left: 122px; }
  .card--back  { left: 666px; }
  .card__art {
    position: absolute;
    inset: 0;
    width: 100%;
    height: 100%;
  }
  .wordmark {
    position: absolute;
    left: 0;
    right: 0;
    top: 522px;
    text-align: center;
    font-size: 84px;
    font-weight: 300;
    letter-spacing: 3px;
    color: var(--blue);
    line-height: 1;
  }
  .identity {
    position: absolute;
    left: 28px;
    top: 34px;
    padding-left: 20px;
    border-left: 13px solid var(--blue);
    color: var(--blue);
  }
  .identity__name {
    font-size: 34px;
    font-weight: 300;
    line-height: 1;
    margin-left: -6px;
  }
  .identity__name strong { font-weight: 700; }
  .identity__title {
    font-size: 19px;
    font-weight: 400;
    letter-spacing: 1px;
    margin-top: 6px;
    line-height: 1;
  }
  .contact { list-style: none; position: absolute; left: 26px; top: 156px; }
  .contact__item {
    display: flex;
    align-items: center;
    height: 44px;
    margin-bottom: 53px;
    color: var(--blue);
    font-size: 20px;
    font-weight: 400;
    letter-spacing: 0.3px;
  }
  .contact__icon {
    width: 44px;
    height: 44px;
    margin-right: 22px;
    flex: none;
  }
</style>
</head>
<body>
<main class="canvas">
  <section class="card card--front" aria-label="Card front">
    <div class="wordmark">quilmora</div>
  </section>

  <section class="card card--back" aria-label="Card back">
    <svg class="card__art" viewBox="0 0 347 608" preserveAspectRatio="none" aria-hidden="true">
      <polygon points="347,237 347,353 0,576" fill="var(--blue)"/>
      <polygon points="0,586 347,365 347,608 0,608" fill="var(--blue)"/>
    </svg>

    <header class="identity">
      <h1 class="identity__name">Devin <strong>Holt</strong></h1>
      <p class="identity__title">PRESIDENT</p>
    </header>

    <ul class="contact">
      <li class="contact__item">
        <svg class="contact__icon" viewBox="0 0 44 44" fill="none" stroke="var(--blue)" stroke-width="2.4" aria-hidden="true">
          <rect x="2" y="9" width="40" height="26"/>
          <path d="M2 11 L22 24 L42 11"/>
        </svg>
        sleep@quilmora.com
      </li>
      <li class="contact__item">
        <svg class="contact__icon" viewBox="0 0 44 44" fill="none" stroke="var(--blue)" stroke-width="2.4" stroke-linejoin="round" aria-hidden="true">
          <path d="M12 36 L8 31 Q6 28 9 25 L30 6 Q33 4 35 7 L38 11 Q40 14 37 16 L33 19 L29 15 L16 27 L20 31 L16 35 Q14 38 12 36 Z"/>
          <path d="M10 38 L6 42"/>
        </svg>
        (800) 471-2960
      </li>
      <li class="contact__item">
        <svg class="contact__icon" viewBox="0 0 44 44" fill="none" stroke="var(--blue)" stroke-width="2.4" aria-hidden="true">
          <circle cx="22" cy="22" r="18"/>
          <ellipse cx="22" cy="22" rx="8" ry="18"/>
          <path d="M22 4 V40 M4 22 H40 M7 13 H37 M7 31 H37"/>
        </svg>
        www.quilmora.com
      </li>
    </ul>
  </section>
</main>
</body>
</html>
```